Mindfulness School for Children -- Business Cards

We're looking for business cards for our school directors and owners. We're a mindfulness school for children called little lanterns. Attached are our logos/icons.

```html
<!DOCTYPE html>
<html lang="en">
<head>
<meta charset="utf-8">
<title>little lanterns — Business Cards</title>
<link rel="stylesheet" href="https://fonts.googleapis.com/css2?family=Arimo:wght@400;700&display=swap">
<style>
  :root {
    --backdrop: #c4c4c4;
    --card: #2a2a2a;
    --card-deep: #222222;
    --teal: #3fa7bd;
    --mint: #8fd1a8;
    --ink-light: #f2f2f2;
    --ink-soft: #d9d9d9;
    --stripe: #ffffff;
    --emboss: #1a1a1a;
  }
  * { box-sizing: border-box; margin: 0; padding: 0; }
  html, body { width: 1200px; height: 788px; overflow: hidden; }
  body {
    background: var(--backdrop);
    font-family: "Arimo", Arial, sans-serif;
    position: relative;
  }
  .business-card {
    position: absolute;
    top: 245px;
    width: 520px;
    height: 297px;
    background: var(--card);
    box-shadow: 0 10px 28px rgba(0,0,0,0.35);
    overflow: hidden;
  }
  .card-front { left: 53px; }
  .card-back { left: 627px; background: var(--card-deep); }

  .front-decor {
    position: absolute;
    right: 48px;
    top: 28px;
    width: 130px;
    height: 130px;
    border-radius: 50%;
    background: #303030;
  }
  .brand-name {
    position: absolute;
    left: 34px;
    top: 34px;
    font-size: 30px;
    font-weight: 400;
    color: var(--mint);
    letter-spacing: 0.5px;
  }
  .person {
    position: absolute;
    left: 34px;
    top: 92px;
  }
  .person-name {
    font-size: 19px;
    font-weight: 700;
    color: var(--teal);
    letter-spacing: 0.8px;
  }
  .person-role {
    font-size: 12px;
    color: var(--ink-light);
    margin-top: 3px;
  }
  .contact-list {
    position: absolute;
    left: 34px;
    top: 150px;
    list-style: none;
  }
  .contact-item {
    display: flex;
    align-items: center;
    gap: 7px;
    font-size: 12px;
    color: var(--ink-light);
    line-height: 19px;
  }
  .contact-item svg { width: 10px; height: 10px; flex: none; }
  .divider {
    position: absolute;
    left: 34px;
    right: 34px;
    top: 222px;
    height: 1px;
    background: var(--teal);
  }
  .address {
    position: absolute;
    left: 34px;
    top: 232px;
    font-size: 12px;
    color: var(--ink-light);
  }
  .base-stripe {
    position: absolute;
    left: 0;
    right: 0;
    bottom: 0;
    height: 14px;
    background: var(--stripe);
  }
  .base-accent {
    position: absolute;
    left: 0;
    bottom: 0;
    width: 54px;
    height: 14px;
    background: var(--teal);
  }

  .back-brand {
    position: absolute;
    left: 0;
    right: 0;
    top: 50%;
    transform: translateY(-50%);
    text-align: center;
    font-size: 50px;
    font-weight: 400;
    color: var(--emboss);
    letter-spacing: 0.5px;
  }
</style>
</head>
<body>

<section class="business-card card-front" aria-label="Business card front">
  <div class="front-decor" aria-hidden="true"></div>
  <div class="brand-name">little lanterns</div>
  <div class="person">
    <div class="person-name">MAYA HOLLOWAY</div>
    <div class="person-role">CEO/Founder</div>
  </div>
  <ul class="contact-list">
    <li class="contact-item">
      <svg viewBox="0 0 10 10" aria-hidden="true"><path d="M2 1 L3.6 1 L4.2 3 L3 3.8 Q4 6 6.2 7 L7 5.8 L9 6.4 L9 8 Q8.5 9 7.5 9 Q1 8 1 2.5 Q1 1.5 2 1 Z" fill="var(--teal)"/></svg>
      (00) 5520 1936
    </li>
    <li class="contact-item">
      <svg viewBox="0 0 10 10" aria-hidden="true"><rect x="0.5" y="2" width="9" height="6" fill="var(--teal)"/><path d="M0.5 2 L5 5.5 L9.5 2" stroke="var(--card)" stroke-width="0.9" fill="none"/></svg>
      info@littlelanterns.com
    </li>
    <li class="contact-item">
      <svg viewBox="0 0 10 10" aria-hidden="true"><circle cx="5" cy="5" r="4.2" fill="none" stroke="var(--teal)" stroke-width="1.1"/><ellipse cx="5" cy="5" rx="1.8" ry="4.2" fill="none" stroke="var(--teal)" stroke-width="0.9"/><line x1="0.8" y1="5" x2="9.2" y2="5" stroke="var(--teal)" stroke-width="0.9"/></svg>
      www.littlelanterns.com
    </li>
  </ul>
  <div class="divider"></div>
  <div class="address">Po Box 4126 Cedar Lane Country Name, AB 30218</div>
  <div class="base-stripe"></div>
  <div class="base-accent"></div>
</section>

<section class="business-card card-back" aria-label="Business card back">
  <div class="back-brand">little lanterns</div>
</section>

</body>
</html>
```